Kelvor Engineers: Why you should hire us keepsake

New design. Open to plastic cards. We are an engineering firm that designs cell phone towers and commercial buildings. Please check out our website www.kelvorstruct.com for more details. We want people to remember our card and for it to be useful if possible. We want the same look and feel on these cards to be translated to other marketing material we may need such as brochures.

Target Market(s)

Architects, Developers and Telecommunication Carriers

Industry/Entity Type

Engineering

Contact Information for Business Card

Card with our company colors, logo, and innovative design with elements related to our industry.

Font styles to use
Sans Serif

Colors
9bcb3c
abd036
0255a3

Requirements
Must have
• Sleek and hip design
Nice to have
• Bright lime green and navy coloring that pops with an innovative design.
Should not have
• A basic and boring design

```html
<!DOCTYPE html>
<html lang="en">
<head>
<meta charset="utf-8">
<title>Kelvor Engineers Business Card</title>
<link rel="stylesheet" href="https://fonts.googleapis.com/css2?family=Roboto+Condensed:wght@700&family=Roboto:wght@400;700&display=swap">
<style>
  :root {
    --backdrop: #2b2b2b;
    --navy: #032a5c;
    --lime: #00f000;
    --paper: #f1f1f1;
    --white: #ffffff;
    --ink: #4a4a4a;
    --rule: #0b2a52;
  }
  * { margin: 0; padding: 0; box-sizing: border-box; }
  html, body { width: 1200px; height: 960px; overflow: hidden; }
  body {
    background: var(--backdrop);
    position: relative;
    font-family: "Roboto", Arial, sans-serif;
  }
  .card {
    position: absolute;
    width: 600px;
    height: 342px;
    overflow: hidden;
    box-shadow: 0 3px 8px rgba(0,0,0,0.5);
  }
  .card--front { left: 314px; top: 114px; background: var(--navy); }
  .card--back { left: 311px; top: 472px; background: var(--paper); }

  .brand {
    position: absolute;
    left: 0; right: 0;
    text-align: center;
    font-family: "Roboto Condensed", "Arial Narrow", sans-serif;
    font-weight: 700;
    color: var(--lime);
    line-height: 1;
    letter-spacing: 1px;
  }
  .card--front .brand { top: 62px; font-size: 84px; }
  .card--back .brand { top: 118px; font-size: 96px; }

  .holder-name {
    position: absolute;
    top: 213px; left: 0; right: 0;
    text-align: center;
    font-family: "Roboto Condensed", "Arial Narrow", sans-serif;
    font-weight: 700;
    font-size: 22px;
    color: var(--lime);
  }
  .contact-line {
    position: absolute;
    top: 245px; left: 0; right: 0;
    text-align: center;
    font-size: 14.5px;
    color: var(--white);
  }
  .contact-line .label { color: var(--lime); font-weight: 700; }

  .web-band {
    position: absolute;
    left: 0; bottom: 0;
    width: 600px; height: 36px;
  }
  .web-address {
    position: absolute;
    left: 0; right: 0; bottom: 10px;
    text-align: center;
    font-weight: 700;
    font-size: 13px;
    letter-spacing: 3.5px;
    color: var(--white);
  }

  .tagline {
    position: absolute;
    top: 266px; left: 0; right: 0;
    display: flex;
    justify-content: center;
    align-items: center;
    gap: 2px;
    font-weight: 700;
    font-size: 16.5px;
    color: var(--lime);
  }
  .tagline::before, .tagline::after {
    content: "";
    width: 30px;
    height: 1.5px;
    background: var(--rule);
  }
  .locations {
    position: absolute;
    top: 288px; left: 0; right: 0;
    text-align: center;
    font-size: 15.5px;
    letter-spacing: 0.6px;
    color: var(--ink);
  }
</style>
</head>
<body>
  <section class="card card--front">
    <div class="brand">KELVOR</div>
    <div class="holder-name">DANA HOLLOWAY REYES</div>
    <div class="contact-line">
      <span class="label">P:</span> 555.014.2210
      <span class="label">M:</span> 555.019.4476
      <span class="label">E:</span> dreyes@kelvorstruct.com
    </div>
    <svg class="web-band" viewBox="0 0 600 36" aria-hidden="true">
      <polygon points="0,0 474,0 486,18 498,0 600,0 600,36 0,36" fill="#00f000"/>
    </svg>
    <div class="web-address">www.kelvorstruct.com</div>
  </section>

  <section class="card card--back">
    <div class="brand">KELVOR</div>
    <div class="tagline">MULTI-DISCIPLINE ENGINEERING</div>
    <div class="locations">Brookvale | Marston | Ellery | Dunmore Bay</div>
  </section>
</body>
</html>
```